Harwick State College Sales Presentation to demonstrate instructional design process

We would like the Powerpoint to be re-designed. The content on the screen and in the notes sections must remain the same but it can all be re-styled to look more modern and professional. Please use our logo colors and the final design should communicate professionalism and experience. We typically use the blue and white colors predominately and use the red in the logo sparingly for emphasis.

Target Market(s)

Audience of college educators, sales people, instructional designers, and leaders

Industry/Entity Type

Higher Education and Professional Services

Font styles to use
Sans Serif

Colors
0054AA
0677BA
7BADD7
CADEEF
E8F1F8
EB3D1F
EC4F4E
F09395
F8D3D4
FCEDEE

Requirements
Must have
• clear visuals, same verbiage we have supplied, colorful and artful design
Nice to have
• some animations between slides would be nice.
Should not have
• It should not use red text on black backgrounds.

```html
<!DOCTYPE html>
<html lang="en">
<head>
<meta charset="utf-8">
<title>Harwick State College – Instructional Design Presentation</title>
<link href="https://fonts.googleapis.com/css2?family=Nunito:wght@400;600;700;800;900&display=swap" rel="stylesheet">
<style>
  :root{
    --canvas:#c9cacc;
    --white:#ffffff;
    --brand-blue:#0054aa;
    --box-blue:#2c68bb;
    --deep-blue:#1757b0;
    --navy:#0a2160;
    --navy-rounded:#13317e;
    --red:#a3161a;
    --ink:#33363d;
    --rule:#3d6fb8;
  }
  *{margin:0;padding:0;box-sizing:border-box}
  html,body{width:1200px;height:4054px;overflow:hidden}
  body{background:var(--canvas);font-family:"Nunito",sans-serif;color:var(--ink);position:relative}
  .slide{position:absolute;left:99px;width:1002px;height:564px;overflow:hidden;background:var(--white)}
  .photo{position:absolute}
  .brand{position:absolute;display:flex;align-items:center;gap:10px;z-index:2}
  .brand-dot{width:40px;height:40px;border-radius:50%;background:var(--brand-blue);flex:none}
  .brand-name{font-weight:800;font-size:30px;color:var(--brand-blue);letter-spacing:.2px}

  /* slide 1 */
  .s1{top:128px}
  .s1 .photo{inset:0;background:linear-gradient(100deg,#f3f4f4 0%,#e7e8e7 35%,#cfc4b7 55%,#e9e9e8 75%,#f4f4f3 100%)}
  .title-box{position:absolute;left:44px;top:328px;width:296px;height:194px;background:var(--box-blue);color:var(--white);padding:28px 24px 0 37px}
  .title-box .lead{font-size:16px;line-height:19px;font-weight:400}
  .title-box .rfp{margin-top:13px;font-size:16px;line-height:19px;font-weight:900;text-transform:uppercase}

  /* slide 2 */
  .s2{top:775px}
  .s2 .photo{left:443px;top:0;width:559px;height:564px;background:linear-gradient(110deg,#6b6e68 0%,#8f9286 40%,#a9aba0 65%,#786f62 100%)}
  .s2 .heading{position:absolute;left:255px;top:41px;font-size:16px;font-weight:800;color:var(--brand-blue);text-transform:uppercase}
  .facts{position:absolute;left:0;top:120px;width:443px;list-style:none}
  .fact{position:relative;padding:0 72px 0 108px;border-bottom:2px solid var(--rule)}
  .fact:last-child{border-bottom:none}
  .fact::before{content:"";position:absolute;left:57px;width:28px;height:28px;border-radius:50%;background:var(--brand-blue)}
  .fact h3{font-size:15px;font-weight:900;color:var(--brand-blue);text-transform:uppercase}
  .fact p{font-size:12.5px;line-height:20px;color:var(--ink);margin-top:4px}
  .f1{height:104px;padding-top:20px}.f1::before{top:24px}
  .f2{height:88px;padding-top:22px}.f2::before{top:28px}
  .f3{height:123px;padding-top:20px}.f3::before{top:22px}
  .f4{height:110px;padding-top:28px}.f4::before{top:34px}

  /* slide 3 */
  .s3{top:1422px}
  .s3 .photo{inset:0;background:linear-gradient(100deg,#b7c0c4 0%,#d8dbd7 35%,#cfc9c0 55%,#e6e7e6 75%,#8f9aa5 100%)}
  .section-box{position:absolute;left:0;top:233px;width:388px;height:161px;background:var(--navy-rounded);border-radius:0 34px 34px 0;color:var(--white);text-align:right;padding:32px 54px 0 0}
  .section-box h2{font-size:40px;font-weight:900;letter-spacing:1px;line-height:44px}
  .section-box p{font-size:18px;font-weight:800;margin-top:4px}

  /* slide 4 */
  .s4{top:2069px}
  .s4 .panel{position:absolute;left:505px;top:0;width:497px;height:564px;background:var(--navy)}
  .s4 .photo{left:0;top:104px;width:518px;height:354px;background:linear-gradient(100deg,#a9a49e 0%,#7b5d4e 30%,#c4b4a7 55%,#5d4d48 75%,#d6d2cd 100%)}
  .philosophy{position:absolute;left:592px;top:146px;width:340px;color:var(--white)}
  .philosophy h2{font-size:19px;font-weight:900;line-height:32px;text-transform:uppercase}
  .philosophy ul{list-style:none;margin-top:28px}
  .philosophy li{position:relative;padding-left:24px;font-size:12.5px;line-height:22px;margin-bottom:31px}
  .philosophy li::before{content:"";position:absolute;left:3px;top:6px;border-left:6px solid var(--white);border-top:5px solid transparent;border-bottom:5px solid transparent}

  /* slide 5 */
  .s5{top:2716px}
  .s5 .photo{inset:0;background:linear-gradient(100deg,#8aa3b4 0%,#c7b299 25%,#e4e3e0 45%,#eef2f5 70%,#f6f7f8 100%)}
  .tag{position:absolute;left:643px;width:285px;color:var(--white);font-size:19px;font-weight:900;text-transform:uppercase;padding-left:38px;line-height:22px;display:flex;align-items:center}
  .tag-blue{top:200px;height:104px;background:var(--deep-blue)}
  .tag-red{top:324px;height:106px;background:var(--red)}

  /* slide 6 */
  .s6{top:3363px}
  .s6 .photo{inset:0;background:linear-gradient(120deg,#0d2d7e 0%,#153b92 40%,#1b46a3 60%,#0c2a78 100%)}
  .thanks{position:absolute;left:375px;top:217px;width:244px;height:76px;border-top:2px solid var(--white);border-bottom:2px solid var(--white);display:flex;align-items:center;justify-content:center;color:var(--white);font-size:36px;font-weight:900;letter-spacing:.5px}
  .contact{position:absolute;left:0;width:1002px;top:410px;text-align:center;color:var(--white);font-size:19px;line-height:38px;list-style:none}
  .s6 .brand-dot{background:var(--white)}
  .s6 .brand-name{color:var(--white)}
</style>
</head>
<body>

<section class="slide s1">
  <div class="photo" role="img" aria-label="Photo of a professional woman in glasses working on a laptop in a bright office"></div>
  <div class="brand" style="left:36px;top:28px"><span class="brand-dot"></span><span class="brand-name">Loomway</span></div>
  <div class="title-box">
    <p class="lead">Harwick State College Public Institutions of Higher Education Request for Proposal</p>
    <p class="rfp">Furnish and Deliver Instructional Design and Media Production 1JNM2303</p>
  </div>
</section>

<section class="slide s2">
  <div class="brand" style="left:30px;top:25px"><span class="brand-dot"></span><span class="brand-name">Loomway</span></div>
  <h2 class="heading">About Loomway</h2>
  <ul class="facts">
    <li class="fact f1"><h3>Woman/Minority Business</h3><p>Certified Harwick State WMBE Woman/<br>Minority Business Enterprise</p></li>
    <li class="fact f2"><h3>17 Years of Experience</h3><p>In Business since 2006</p></li>
    <li class="fact f3"><h3>Primary Focus</h3><p>We are dedicated to creating top-notch educational experiences through collaboration with faculty and subject matter experts.</p></li>
    <li class="fact f4"><h3>Principles</h3><p>Communication, attention, and passion</p></li>
  </ul>
  <div class="photo" role="img" aria-label="Photo of a woman in glasses and a green shirt working on a laptop"></div>
</section>

<section class="slide s3">
  <div class="photo" role="img" aria-label="Photo of a smiling woman in a team meeting with colleagues around a table"></div>
  <div class="brand" style="left:74px;top:20px"><span class="brand-dot"></span><span class="brand-name">Loomway</span></div>
  <div class="section-box"><h2>PROCESS</h2><p>Overview of Our Process</p></div>
</section>

<section class="slide s4">
  <div class="panel"></div>
  <div class="brand" style="left:18px;top:20px"><span class="brand-dot"></span><span class="brand-name">Loomway</span></div>
  <div class="photo" role="img" aria-label="Photo of four women collaborating around a laptop at a table"></div>
  <div class="philosophy">
    <h2>Our Process<br>Philosophy</h2>
    <ul>
      <li>Inspire Faculty</li>
      <li>Deliver Powerful and Effective Course Designs</li>
      <li>Equip Faculty with Cutting-Edge Concepts,<br>Tools, Research, and Best Practices</li>
    </ul>
  </div>
</section>

<section class="slide s5">
  <div class="photo" role="img" aria-label="Photo of two smiling women looking at a laptop together in an office"></div>
  <div class="brand" style="left:643px;top:98px"><span class="brand-dot"></span><span class="brand-name">Loomway</span></div>
  <div class="tag tag-blue">Resource Rich</div>
  <div class="tag tag-red">10-Week Engagement<br>Model</div>
</section>

<section class="slide s6">
  <div class="photo" role="img" aria-label="Blue-tinted photo of a team working together"></div>
  <div class="thanks">THANK YOU!</div>
  <ul class="contact">
    <li>Dana Whitcombe</li>
    <li>whitcombe@example.com</li>
    <li>555-0142</li>
  </ul>
  <div class="brand" style="left:35px;top:497px"><span class="brand-dot"></span><span class="brand-name">Loomway</span></div>
</section>

</body>
</html>
```